Need App for Impact Related Events

My app is to help with internal events. When you enter the prompted event code the next screen shows you everyone currently at the event. It will give you the ability to Start a conversation with someone you met at that event, or signal it is your turn to send a message. The next screen is a message thread with that person. I am looking for a design that incorporates the colors and ‘feel good’ emotion of our logo. I have pieced together a pretty good interpretation of what I’m looking for in the attached mockup by slicing and dicing designs. I also attached our logo mascot.Screens (see attached mockups)

Note 1: I do not like the picture on the screen used in screen one because it makes it seem like a dating app. I attached an alternative photo that can be used or present different ideas.

Note 2: On the login/signup screen (screen 2) I need an additional first and last name for login, you can try to fit this on one login screen or present a two step signup screen where that is presented in the second screen.

READ MOCKUP GUIDELINES UNDER Must Haves

Target Market(s)

People attending internal social impact events

Industry/Entity Type

Charity

Font styles to use
Sans Serif

Colors
86cfc6

Requirements
Must have
• Follow the screen mockups attached to project
• PLEASE READ
• I have provided a relatively close design of what I’m looking for in the mockups. Some screens need to be followed more closely to my design mockup than other. I have listed a guide below how how closely you should follow my mockup design exactly. Overall I would like to see some ideas of incorporating a few accent colors so it doesn’t appear SO Blue. I also attached some app inspiration designs I found from around the web
• Screen Mockup Guideline Follow %
• Screen 1: 65% - mostly on target, would like to see ways to make it not SO Blue and possibly creative places to add some explainer text describing the app
• Screen 2: 50% - general design idea is here, but more open
• Screen 3: 35% - a lot more room for design influence
• Screen 4: 70% - mostly on target, a little room for design influence/color scheme ideas
• Screen 5-6: 25% - a lot of room for design change/ideas/influence
• Screen 7-8: 80% - already very close to what I need, maybe open to slight sizing and color scheme ideas
• Screen 9: 15% - the most open for influence, only the general functionality of the screen is communicated here
Nice to have
• Please Read Mockup Guideline above. In large part I am looking for something to use some nice accent colors so it is not overwhelmingly blue and bring the whole design into a seamless style.
Should not have

```html
<!DOCTYPE html>
<html lang="en">
<head>
<meta charset="utf-8">
<title>Create Event – Event Code</title>
<link href="https://fonts.googleapis.com/css2?family=Nunito:wght@300;400;600;700;800&display=swap" rel="stylesheet">
<style>
  :root{
    --bg:#6fe0dd;
    --title:#1b9f9d;
    --accent:#1fcbc6;
    --accent-dark:#1fb6b1;
    --field-line:rgba(24,160,158,0.18);
    --field-fill:rgba(255,255,255,0.06);
    --placeholder:#38b6b3;
    --card:#ffffff;
    --ink:#1f2a2e;
    --muted:#4a5559;
    --avatar:#4f8f8c;
  }
  *{box-sizing:border-box;margin:0;padding:0}
  html,body{width:675px;height:1200px;overflow:hidden}
  body{background:var(--bg);font-family:"Nunito",sans-serif;position:relative}

  .screen-title{position:absolute;left:30px;top:38px;font-size:50px;font-weight:800;color:var(--title);letter-spacing:0.3px}
  .avatar{position:absolute;left:579px;top:37px;width:64px;height:64px;border-radius:50%;
    background:radial-gradient(circle at 45% 40%,#8fb9b4,var(--avatar))}

  .field{position:absolute;left:56px;width:563px;border:2px solid var(--field-line);border-radius:6px;background:var(--field-fill)}
  .field-label{position:absolute;left:26px;top:20px;font-size:26px;font-weight:400;color:var(--placeholder)}
  .field-name{top:141px;height:75px}
  .field-category{top:234px;height:75px}
  .field-category svg{position:absolute;right:26px;top:26px}
  .field-details{top:328px;height:291px}
  .field-time{top:652px;height:64px}
  .field-time .field-label{top:14px}

  .code-dialog{position:absolute;left:88px;top:304px;width:501px;height:594px;background:var(--card);border-radius:8px;
    box-shadow:0 6px 24px rgba(0,90,90,0.18);text-align:center}
  .dialog-title{margin-top:26px;font-size:36px;font-weight:600;color:var(--ink)}
  .event-code{margin-top:100px;font-size:38px;font-weight:700;color:var(--accent);letter-spacing:2px}
  .dialog-note{margin-top:52px;font-size:23px;line-height:32px;font-weight:300;color:var(--muted)}
  .dismiss-button{position:absolute;left:100px;top:468px;width:300px;height:74px;border:none;border-radius:6px;
    background:var(--accent);color:#fff;font-family:"Nunito",sans-serif;font-size:22px;font-weight:800;letter-spacing:2px;
    box-shadow:0 3px 8px rgba(0,120,120,0.25)}

  .tab-bar{position:absolute;left:0;top:1080px;width:675px;height:120px}
  .tab-icon{position:absolute;top:48px}
  .fab{position:absolute;left:285px;top:0;width:106px;height:106px;border-radius:50%;background:var(--accent);
    display:flex;align-items:center;justify-content:center;box-shadow:0 4px 12px rgba(0,110,110,0.22)}
</style>
</head>
<body>
  <h1 class="screen-title">Create Event</h1>
  <div class="avatar" role="img" aria-label="Profile photo of the signed-in user"></div>

  <div class="field field-name"><span class="field-label">Event Name</span></div>
  <div class="field field-category"><span class="field-label">Catagory</span>
    <svg width="32" height="20" viewBox="0 0 32 20"><path d="M2 3 L16 17 L30 3" fill="none" stroke="var(--accent-dark)" stroke-width="3.5" stroke-linecap="round" stroke-linejoin="round"/></svg>
  </div>
  <div class="field field-details"></div>
  <div class="field field-time"><span class="field-label">Time</span></div>

  <section class="code-dialog">
    <h2 class="dialog-title">Your Event Code</h2>
    <p class="event-code">A34FVVG5</p>
    <p class="dialog-note">Share this code with the people you<br>want to invite to this event.<br>Don’t forget to mention that they’ll<br>need “Kind Circle” app to enter<br>this code.</p>
    <button class="dismiss-button">DISMISS</button>
  </section>

  <nav class="tab-bar">
    <svg class="tab-icon" style="left:44px" width="48" height="48" viewBox="0 0 48 48" fill="none" stroke="var(--accent-dark)" stroke-width="3.5" stroke-linecap="round">
      <rect x="4" y="8" width="40" height="36" rx="3"/><line x1="4" y1="18" x2="44" y2="18"/><line x1="14" y1="3" x2="14" y2="12"/><line x1="34" y1="3" x2="34" y2="12"/>
    </svg>
    <svg class="tab-icon" style="left:180px" width="46" height="46" viewBox="0 0 46 46" fill="none" stroke="var(--accent-dark)" stroke-width="3.5" stroke-linejoin="round">
      <path d="M23 4 A19 19 0 1 1 8 35 L4 42 L13 39 A19 19 0 0 0 23 42"/>
      <path d="M23 4 A19 19 0 0 0 8 35"/>
    </svg>
    <div class="fab">
      <svg width="34" height="34" viewBox="0 0 34 34" stroke="#ffffff" stroke-width="3" stroke-linecap="round"><line x1="4" y1="4" x2="30" y2="30"/><line x1="30" y1="4" x2="4" y2="30"/></svg>
    </div>
    <svg class="tab-icon" style="left:450px" width="44" height="48" viewBox="0 0 44 48" fill="none" stroke="var(--accent-dark)" stroke-width="3.5" stroke-linejoin="round" stroke-linecap="round">
      <path d="M8 36 V22 A14 14 0 0 1 36 22 V36 Z"/><line x1="3" y1="36" x2="41" y2="36"/><path d="M17 42 A5 5 0 0 0 27 42"/><line x1="22" y1="4" x2="22" y2="8"/>
    </svg>
    <svg class="tab-icon" style="left:584px" width="48" height="44" viewBox="0 0 48 44" fill="none" stroke="var(--accent-dark)" stroke-width="3.5" stroke-linecap="round">
      <line x1="3" y1="12" x2="45" y2="12"/><line x1="3" y1="32" x2="45" y2="32"/>
      <circle cx="32" cy="12" r="6" fill="var(--bg)"/><circle cx="16" cy="32" r="6" fill="var(--bg)"/>
    </svg>
  </nav>
</body>
</html>
```